home accents e-commerce website

I'd like a professional simple website designed where I can sell my home goods. I already have my domain name registered. I need the website to accept credit card payments and Monvex. It should have a shopping cart option and calculate sales tax and shipping costs on merchandise automatically.

I'll be taking photographs of the merchandise and writing product descriptions myself. (I'm not a professional photographer, so these photos probably won't look too polished. If you can help me make them look better, that'd be great). As I add new merchandise in the future, I'd like an option where I can log in to the back end myself and add pictures/product descriptions. And take old products down as they sell out. So the website needs to be user-friendly for me, even though I'm completely web design illiterate!

I'd like a creative, talented person who can create a whimsical, cute website. Nothing too corporate-looking.

Thank you!

Target Market(s)

women, online shoppers, New York City-area, (ship products to the United States only)

Industry/Entity Type

Home And Garden

Coding

Coded - Design and coding required

Number of Pages Required

1 page

Font styles to use
Sans Serif

Colors
0355a3
ffffff

Requirements
Must have
• shopping cart feature
• safe, secure credit card and Monvex payments
• ability for me to go in and add new products and take down old/sold products
Nice to have
• whimsical, cute design
Should not have
• too corporate-looking

```html
<!DOCTYPE html>
<html lang="en">
<head>
<meta charset="utf-8">
<title>Nestwell Home Goods</title>
<link href="https://fonts.googleapis.com/css2?family=Raleway:wght@400;500;600;700;800&family=Montserrat:wght@600;700;800&display=swap" rel="stylesheet">
<style>
:root{
  --brand:#0355a3;
  --white:#ffffff;
  --ink:#555555;
  --ink-dark:#444444;
  --line:#dddddd;
  --band:#f2f2f2;
  --icon:#6b6b6b;
}
*{box-sizing:border-box;margin:0;padding:0}
html,body{width:910px;height:1200px;overflow:hidden;background:var(--white)}
body{font-family:"Raleway",sans-serif;color:var(--ink);position:relative}
a{color:inherit;text-decoration:none}

.site-header{position:absolute;left:57px;top:14px;width:797px;height:70px}
.brand{position:absolute;left:0;top:4px;color:var(--brand)}
.brand-name{font-family:"Raleway",sans-serif;font-weight:800;font-size:38px;line-height:40px;letter-spacing:1px}
.brand-sub{font-weight:500;font-size:11.5px;letter-spacing:6.6px;margin-top:0}
.social{position:absolute;display:flex;gap:13px}
.social span{width:16px;height:16px;border-radius:50%;background:var(--icon);display:block}
.header-social{right:100px;top:5px}
.cart{position:absolute;right:0;top:0;display:flex;align-items:center;gap:8px;font-family:"Montserrat",sans-serif;font-weight:700;font-size:9.5px;color:var(--ink-dark);letter-spacing:.3px}
.cart-icon{width:25px;height:25px;border-radius:50%;background:var(--brand);display:flex;align-items:center;justify-content:center}
.main-nav{position:absolute;right:0;top:49px;display:flex;gap:34px;font-family:"Montserrat",sans-serif;font-weight:600;font-size:9.5px;color:var(--ink-dark)}
.main-nav .active{color:var(--brand)}

.categories{position:absolute;left:57px;top:98px;width:182px;height:285px;border:2px solid #e4e4e4;border-top:none}
.categories h2{background:var(--brand);color:var(--white);font-family:"Montserrat",sans-serif;font-weight:600;font-size:11.5px;height:38px;line-height:38px;padding-left:13px;letter-spacing:.2px}
.categories ul{list-style:none}
.categories li{height:27.3px;line-height:27px;font-size:10px;color:var(--ink-dark);border-bottom:1px dashed #cfcfcf;padding-left:14px;display:flex;gap:20px}
.categories li:last-child{border-bottom:none}

.hero{position:absolute;left:252px;top:98px;width:602px;height:285px;border:2px solid #e4e4e4}
.hero-photo{position:absolute;inset:0;background:linear-gradient(90deg,#e9e4db 0%,#d9d3c8 45%,#b9b6b1 100%)}
.hero-photo .blanket-blue{position:absolute;left:60px;top:10px;width:240px;height:130px;border-radius:60px;background:#253a5e}
.hero-photo .blanket-red{position:absolute;left:80px;top:170px;width:280px;height:110px;border-radius:30px;background:#d41f22}
.hero-card{position:absolute;left:353px;top:58px;width:214px;height:168px;background:rgba(70,70,70,.85);text-align:center;color:var(--white)}
.hero-card h1{font-family:"Montserrat",sans-serif;font-weight:800;font-size:26px;line-height:29px;letter-spacing:1px;margin-top:22px}
.btn-solid{display:inline-block;background:var(--brand);color:var(--white);font-family:"Montserrat",sans-serif;font-weight:600;font-size:10.5px}
.hero-card .btn-solid{width:155px;height:31px;line-height:31px;margin-top:10px}
.dots{display:flex;gap:6px;justify-content:center;margin-top:22px}
.dots span{width:9px;height:9px;border-radius:2px;background:var(--white)}
.dots span:first-child{background:var(--brand)}

.featured-title{position:absolute;left:0;width:910px;top:416px;text-align:center;font-family:"Montserrat",sans-serif;font-weight:600;font-size:19px;color:var(--ink-dark);letter-spacing:.5px}
.products{position:absolute;left:57px;top:479px;width:797px;display:flex}
.product{flex:1;height:258px;text-align:center;border-right:1px solid var(--line)}
.product:last-child{border-right:none}
.product-photo{width:120px;height:120px;margin:12px auto 0;border-radius:8px}
.product h3{font-family:"Montserrat",sans-serif;font-weight:600;font-size:11px;color:var(--brand);margin-top:14px}
.product p{font-size:11px;line-height:17px;margin-top:6px;color:var(--ink)}
.price{font-family:"Montserrat",sans-serif;font-weight:700;font-size:17px;color:var(--brand);margin-top:6px}
.btn-outline{display:inline-block;border:2px solid var(--brand);color:var(--brand);font-family:"Montserrat",sans-serif;font-weight:600;font-size:8.5px;width:84px;height:27px;line-height:23px;margin-top:12px}

.about-band{position:absolute;left:0;top:784px;width:910px;height:245px;background:var(--band)}
.about{position:absolute;left:57px;top:30px;width:594px}
.about h2{font-family:"Montserrat",sans-serif;font-weight:600;font-size:19px;color:var(--ink-dark);letter-spacing:.5px}
.about p{font-size:10.8px;line-height:19px;margin-top:10px;color:var(--ink)}
.about .btn-solid{width:115px;height:34px;line-height:34px;text-align:center;margin-top:22px;font-size:11px}
.newsletter{position:absolute;left:670px;top:32px;width:184px;height:180px;background:var(--white);padding:20px 14px 0}
.newsletter h2{text-align:center;font-family:"Montserrat",sans-serif;font-weight:600;font-size:18px;color:var(--ink-dark);letter-spacing:.5px}
.field{height:32px;border:1px solid #cfcfcf;margin-top:5px;text-align:center;line-height:30px;font-size:10px;color:var(--ink)}
.field:first-of-type{margin-top:14px}
.newsletter .btn-solid{display:block;width:100%;height:32px;line-height:32px;text-align:center;margin-top:6px}

.site-footer{position:absolute;left:57px;top:1064px;width:797px;height:110px}
.footer-brand .brand-name{font-size:28px;line-height:30px}
.footer-brand .brand-sub{font-size:9px;letter-spacing:5.2px}
.footer-brand{color:var(--brand)}
.copyright{font-size:9.5px;line-height:16px;color:var(--ink-dark);margin-top:14px}
.footer-col{position:absolute;top:0}
.footer-col h4{font-family:"Montserrat",sans-serif;font-weight:700;font-size:10.5px;color:var(--brand);margin-bottom:6px}
.footer-col li{list-style:none;font-size:9.8px;line-height:22.4px;color:var(--ink)}
.cards{display:flex;gap:8px;margin-top:4px}
.cards span{width:24px;height:15px;border-radius:2px;background:#9a9a9a;color:var(--white);font-size:6px;line-height:15px;text-align:center;font-weight:600}
.footer-social{position:relative;margin-top:24px;gap:14px}
</style>
</head>
<body>

<header class="site-header">
  <div class="brand">
    <div class="brand-name">nestwell</div>
    <div class="brand-sub">HOME GOODS</div>
  </div>
  <div class="social header-social" aria-label="Social links"><span></span><span></span><span></span><span></span></div>
  <a class="cart" href="#">
    <span class="cart-icon"><svg width="11" height="10" viewBox="0 0 11 10"><path d="M0 1h2l1.5 5h5.5l1.5-4H3" fill="none" stroke="#fff" stroke-width="1.4"/><circle cx="4" cy="8.5" r="1" fill="#fff"/><circle cx="8.5" cy="8.5" r="1" fill="#fff"/></svg></span>
    MY CART
  </a>
  <nav class="main-nav">
    <a class="active" href="#">HOME</a>
    <a href="#">ABOUT NESTWELL</a>
    <a href="#">HOW DOES THIS CRAZINESS WORK?</a>
    <a href="#">CONTACT</a>
  </nav>
</header>

<aside class="categories">
  <h2>PRODUCT CATEGORIES</h2>
  <ul>
    <li><span>›</span>Vases</li>
    <li><span>›</span>Throw Pillows</li>
    <li><span>›</span>Blankets and Throws</li>
    <li><span>›</span>For Your Floors</li>
    <li><span>›</span>For Your Walls</li>
    <li><span>›</span>For Your Table</li>
    <li><span>›</span>For Your Bedside</li>
    <li><span>›</span>Let THere Be Light</li>
    <li><span>›</span>Put Your Feet Up</li>
  </ul>
</aside>

<section class="hero">
  <div class="hero-photo" role="img" aria-label="Photo of a rolled navy blanket and folded red blanket on a wooden shelf">
    <div class="blanket-blue"></div>
    <div class="blanket-red"></div>
  </div>
  <div class="hero-card">
    <h1>BLANKET &amp;<br>THROWS</h1>
    <a class="btn-solid" href="#">SHOP NOW</a>
    <div class="dots"><span></span><span></span><span></span><span></span></div>
  </div>
</section>

<h2 class="featured-title">FEATURED PRODUCT</h2>
<section class="products">
  <article class="product">
    <div class="product-photo" role="img" aria-label="Photo of an antique wall clock on a wrought bracket" style="background:radial-gradient(circle at 55% 58%,#d9cfb8 0 30%,#5a3f25 31% 38%,#fff 40%)"></div>
    <h3>PRODUCT NAME</h3><p>Vestibulum ante ipsum<br>primis in faucibus</p><div class="price">$21.00</div><a class="btn-outline" href="#">ADD TO CART</a>
  </article>
  <article class="product">
    <div class="product-photo" role="img" aria-label="Photo of a folded blue knit blanket" style="width:170px;background:radial-gradient(ellipse at 50% 50%,#3f7fbf 0 45%,#fff 60%)"></div>
    <h3>PRODUCT NAME</h3><p>Vestibulum ante ipsum<br>primis in faucibus</p><div class="price">$21.00</div><a class="btn-outline" href="#">ADD TO CART</a>
  </article>
  <article class="product">
    <div class="product-photo" role="img" aria-label="Photo of white and mauve throw pillows" style="width:160px;background:linear-gradient(160deg,#fff 15%,#ececec 35%,#c7a0b2 60%,#fff 85%)"></div>
    <h3>PRODUCT NAME</h3><p>Vestibulum ante ipsum<br>primis in faucibus</p><div class="price">$21.00</div><a class="btn-outline" href="#">ADD TO CART</a>
  </article>
  <article class="product">
    <div class="product-photo" role="img" aria-label="Photo of a colourful striped ceramic vase" style="width:100px;background:linear-gradient(180deg,#fff 8%,#e83d6a 30%,#f5a33a 45%,#4fb3d9 60%,#e2405c 75%,#3a2e2a 88%,#fff 95%)"></div>
    <h3>PRODUCT NAME</h3><p>Vestibulum ante ipsum<br>primis in faucibus</p><div class="price">$21.00</div><a class="btn-outline" href="#">ADD TO CART</a>
  </article>
</section>

<section class="about-band">
  <div class="about">
    <h2>ABOUT NESTWELL</h2>
    <p>Aliquam molestie, mi et imperdiet euismod, dui purus auctor tellus, et interdum lacus lectus et ante. Sed accumsan sollicitudin sapien, sit amet adipiscing turpis gravida ac. In congue, neque ac lobortis volutpat, libero mauris varius mi, vitae suscipit ipsum ligula vitae risus. Duis aliquam nibh a dui iaculis viverra id a velit. Vivamus egestas risus in magna varius commodo. Sed semper viverra egestas. Etiam pretium porttitor lectus, vel ornare neque porta volutpat. Suspendisse lobortis turpis in odio blandit ac interdum lorem euismod.</p>
    <a class="btn-solid" href="#">READ MORE</a>
  </div>
  <form class="newsletter">
    <h2>NEWSLETTER</h2>
    <div class="field">Enter Name</div>
    <div class="field">Enter Email Address</div>
    <a class="btn-solid" href="#">SUBSCRIBE</a>
  </form>
</section>

<footer class="site-footer">
  <div class="footer-brand">
    <div class="brand-name">nestwell</div>
    <div class="brand-sub">HOME GOODS</div>
    <div class="copyright">Copyright © 2017. Company Name<br>All Right Reserved</div>
  </div>
  <div class="footer-col" style="left:202px"><h4>SITE MAP</h4><ul><li>Home</li><li>About Nestwell</li><li>How does this Craziness Work?</li><li>Contact</li></ul></div>
  <div class="footer-col" style="left:388px"><h4>MY ACCOUNT</h4><ul><li>My Account</li><li>Log In</li><li>Register</li><li>My Cart</li></ul></div>
  <div class="footer-col" style="left:524px"><h4>SUPPORT</h4><ul><li>Vestibulum</li><li>Ante ipsum primis</li><li>Faucibus orci</li><li>Luctus et ultrices</li></ul></div>
  <div class="footer-col" style="left:660px"><h4>WE ACCEPTED</h4>
    <div class="cards"><span>Monvex</span><span>Mercora</span><span>Vantra</span><span>Dexa</span></div>
    <div class="social footer-social"><span></span><span></span><span></span><span></span></div>
  </div>
</footer>

</body>
</html>
```